Church needs a street sign design

We're a small church located in Silicon Valley, California. Our website is https://www.vgtmarlowfield.org/ and our address is 4817 Ferrow Ave, San Jose, California, 95873. You can look up our location on Google Maps to see the sign from Street View. I have uploaded an image of the street sign as well. The marquee, the top section of the sign, and the separating line between them both will be removed. We're seeking a design for a new backlit acrylic insert that will go on the front of the light box and the back of the lightbox. The acrylic sign will fill the entire external frame. In the future, we may build a decorative wood frame around the structural legs, as visualized in one of the uploaded files. The church's brand colors are: #003366 (dark blue), #ff6600 (vibrant orange), #228b22 (forest green). I have also uploaded the church's logo assets. Our primary font is Montserrat and the secondary is Poppins. You can deviate from these colors/fonts if the sign is still coherent with the rest of our branding. Our branding values are mission, truth, passion, and community (please do not put those words on the sign! They are just intended to guide the look of the design). The sign dimensions are 96" by 47.5". Keep in mind that the sign will be backlit on a busy street side. It will also be positioned next to an old-looking church building. We do NOT want a sign that looks traditional, old, or antiquated. Instead, we want a modern-looking sign that pairs well with our old building while helping it look more modern too. We would also like the web address clearly visible on the sign: vgtmarlowfield.org. If you have any questions, just let me know!

```html
<!DOCTYPE html>
<html lang="en">
<head>
<meta charset="utf-8">
<title>Marlowfield Community Church – Faith and Practice</title>
<link href="https://fonts.googleapis.com/css2?family=Abril+Fatface&family=Montserrat:wght@500;600&family=Poppins:wght@400;500;700&display=swap" rel="stylesheet">
<style>
  :root {
    --navy: #223461;
    --pattern-blue: #2c56a6;
    --orange: #e06a35;
    --orange-deep: #d9652f;
    --ink: #1f2c5a;
    --white: #ffffff;
  }
  html, body {
    margin: 0;
    padding: 0;
    overflow: hidden;
    background: var(--navy);
  }
  .sign {
    position: relative;
    width: 1200px;
    height: 592px;
    overflow: hidden;
    background: var(--navy);
  }
  .side-decor {
    position: absolute;
    top: 0;
    height: 592px;
    width: 260px;
  }
  .side-decor--left {
    left: 0;
    background: linear-gradient(90deg, rgba(44,86,166,0.35), rgba(44,86,166,0) );
  }
  .side-decor--right {
    right: 0;
    background: linear-gradient(270deg, rgba(44,86,166,0.35), rgba(44,86,166,0));
  }
  .invite {
    position: absolute;
    left: 440px;
    top: 30px;
    width: 320px;
    height: 100px;
  }
  .invite text {
    font-family: "Montserrat", sans-serif;
    font-weight: 600;
    font-size: 50px;
    letter-spacing: 6px;
  }
  .invite .invite-shadow { fill: var(--white); }
  .invite .invite-face { fill: var(--orange); }
  .church-name {
    position: absolute;
    left: 0;
    width: 1200px;
    top: 140px;
    display: flex;
    justify-content: center;
    align-items: center;
    gap: 10px;
    font-family: "Montserrat", sans-serif;
    font-weight: 600;
    font-size: 18px;
    letter-spacing: 1.5px;
    color: var(--white);
  }
  .church-name .mark {
    width: 14px;
    height: 14px;
    background: var(--white);
  }
  .headline {
    position: absolute;
    left: 0;
    width: 1200px;
    top: 208px;
    margin: 0;
    text-align: center;
    font-family: "Abril Fatface", serif;
    font-weight: 400;
    font-size: 112px;
    line-height: 96px;
    color: var(--white);
  }
  .service-time {
    position: absolute;
    left: 0;
    width: 1200px;
    top: 438px;
    text-align: center;
    font-family: "Poppins", sans-serif;
    font-weight: 500;
    font-size: 31px;
    letter-spacing: 1px;
    color: var(--white);
  }
  .web-band {
    position: absolute;
    left: 210px;
    width: 780px;
    top: 490px;
    height: 73px;
    background: linear-gradient(90deg, rgba(224,106,53,0) 0%, var(--orange-deep) 25%, var(--orange) 50%, var(--orange-deep) 75%, rgba(224,106,53,0) 100%);
  }
  .web-address {
    position: absolute;
    left: 0;
    width: 1200px;
    top: 496px;
    text-align: center;
    font-family: "Poppins", sans-serif;
    font-size: 41px;
    line-height: 56px;
    color: var(--ink);
  }
  .web-address .domain-name { font-weight: 700; }
  .web-address .domain-part { font-weight: 400; }
</style>
</head>
<body>
  <main class="sign">
    <div class="side-decor side-decor--left" role="img" aria-label="Repeating outlined cross pattern in bright blue"></div>
    <div class="side-decor side-decor--right" role="img" aria-label="Repeating outlined cross pattern in bright blue"></div>

    <svg class="invite" viewBox="0 0 320 100" aria-label="Join us">
      <defs>
        <path id="invite-arc" d="M 15 95 Q 160 -15 305 95"/>
        <path id="invite-arc-shadow" d="M 17 97 Q 162 -13 307 97"/>
      </defs>
      <text class="invite-shadow"><textPath href="#invite-arc-shadow" startOffset="50%" text-anchor="middle">JOIN US</textPath></text>
      <text class="invite-face"><textPath href="#invite-arc" startOffset="50%" text-anchor="middle">JOIN US</textPath></text>
    </svg>

    <div class="church-name"><span class="mark"></span><span>MARLOWFIELD COMMUNITY CHURCH</span></div>

    <h1 class="headline">faith and<br>practice</h1>

    <div class="service-time">SUNDAY SERVICE • 10:40 AM</div>

    <div class="web-band"></div>
    <div class="web-address"><span class="domain-part">www.</span><span class="domain-name">vgtmarlowfield</span><span class="domain-part">.org</span></div>
  </main>
</body>
</html>
```